Keystone Trench Co Business Card*

Looking for a professional, clean and crisp business card

I am in the underground utilities industry and am just looking for a really impressive business card. I would like our card to be white with our symbol crisp and clear with it protruding. I also have a business partner that will require his name and info on the card once the design is set. I would like to have our website info on the card which is;
http://keystonetrenchco.example/

Contact Information for Business Card

Website, contact name, number and email

```html
<!DOCTYPE html>
<html lang="en">
<head>
<meta charset="utf-8">
<title>Keystone Trench Co — Business Card</title>
<link href="https://fonts.googleapis.com/css2?family=Open+Sans:wght@400;600;800&display=swap" rel="stylesheet">
<style>
  :root {
    --stage: #d9dadd;
    --card-white: #f4f4f4;
    --ink: #171717;
    --brand-blue: #3560a6;
    --accent-red: #d9242b;
    --paper-shade: #e6e8ee;
    --text-light: #ffffff;
  }
  * { box-sizing: border-box; margin: 0; padding: 0; }
  html, body { width: 1200px; height: 900px; overflow: hidden; }
  body {
    background: var(--stage);
    font-family: "Open Sans", Verdana, sans-serif;
    display: flex; flex-direction: column; align-items: center; justify-content: center; gap: 36px;
  }
  .card {
    position: relative; width: 700px; height: 400px; overflow: hidden;
    box-shadow: 0 10px 30px rgba(0,0,0,.25);
  }
  .card-front { background: var(--card-white); }
  .card-back { background: var(--ink); }
  .card-art { position: absolute; inset: 0; }
  .brand-mark {
    position: absolute; display: flex; align-items: center; gap: 12px;
    font-weight: 800; color: var(--ink); font-size: 26px; letter-spacing: .5px;
  }
  .brand-mark .dot { width: 18px; height: 18px; border-radius: 50%; background: var(--brand-blue); }
  .card-front .brand-mark { left: 48px; top: 70px; }
  .identity { position: absolute; right: 44px; top: 120px; text-align: right; color: var(--ink); }
  .identity .person-name { color: var(--brand-blue); font-weight: 800; font-size: 28px; letter-spacing: 2px; text-transform: uppercase; }
  .identity .role { font-size: 17px; margin-bottom: 12px; }
  .identity .address { font-size: 15px; line-height: 1.35; }
  .contacts {
    position: absolute; right: 210px; bottom: 28px; list-style: none;
    color: var(--text-light); font-size: 15px; text-align: right; line-height: 1.55;
  }
  .contacts li { display: flex; justify-content: flex-end; align-items: center; gap: 10px; }
  .contacts svg { width: 15px; height: 15px; flex: none; }
  .card-back .brand-mark { left: 50%; top: 140px; transform: translateX(-50%); color: #d4d4d4; font-size: 34px; white-space: nowrap; }
  .card-back .brand-mark .dot { background: #d4d4d4; }
  .web-line { position: absolute; left: 0; right: 0; top: 240px; text-align: center; color: var(--text-light); font-size: 20px; }
  .web-line .domain { color: var(--brand-blue); }
</style>
</head>
<body>
  <section class="card card-front">
    <svg class="card-art" viewBox="0 0 700 400" preserveAspectRatio="none">
      <defs>
        <linearGradient id="scene-fade" x1="0" y1="0" x2="1" y2="1">
          <stop offset="0" stop-color="var(--paper-shade)"/>
          <stop offset="1" stop-color="var(--card-white)"/>
        </linearGradient>
      </defs>
      <rect x="20" y="30" width="250" height="200" fill="url(#scene-fade)" role="img" aria-label="Faint mountain scenery behind the company name"/>
      <path d="M0,150 C140,250 380,240 520,290 C580,312 615,350 640,400 L0,400 Z" fill="var(--ink)"/>
      <path d="M0,158 C140,262 380,250 520,300 C575,320 600,355 620,400" fill="none" stroke="var(--card-white)" stroke-width="5"/>
      <path d="M250,235 C420,238 540,262 600,320 C625,345 640,375 655,400 L630,400 C615,360 590,330 560,310 C480,262 360,245 250,235 Z" fill="var(--brand-blue)"/>
    </svg>
    <div class="brand-mark"><span class="dot"></span>Keystone Trench Co</div>
    <div class="identity">
      <p class="person-name">Dale Marrick</p>
      <p class="role">Owner</p>
      <p class="address">Keystone Trench Co Inc.<br>18 Alder Row, Brookvale<br>CA 30412</p>
    </div>
    <ul class="contacts">
      <li>555-014-2290
        <svg viewBox="0 0 16 16"><path d="M4 1 L7 4 L5.5 6 C6.5 8 8 9.5 10 10.5 L12 9 L15 12 L13 15 C7 14 2 9 1 3 Z" fill="var(--accent-red)"/></svg></li>
      <li>dale@keystonetrenchco.example
        <svg viewBox="0 0 16 16"><rect x="1.5" y="3.5" width="13" height="9" fill="none" stroke="var(--accent-red)" stroke-width="1.5"/><path d="M1.5 3.5 L8 9 L14.5 3.5" fill="none" stroke="var(--accent-red)" stroke-width="1.5"/></svg></li>
      <li>www.keystonetrenchco.example
        <svg viewBox="0 0 16 16"><g fill="none" stroke="var(--accent-red)" stroke-width="1.3"><circle cx="8" cy="8" r="6.5"/><ellipse cx="8" cy="8" rx="3" ry="6.5"/><path d="M1.5 8 H14.5 M3 4.5 H13 M3 11.5 H13"/></g></svg></li>
    </ul>
  </section>

  <section class="card card-back">
    <div class="brand-mark"><span class="dot"></span>Keystone Trench Co</div>
    <p class="web-line">www.<span class="domain">keystonetrenchco</span>.example</p>
  </section>
</body>
</html>
```